BRIGHT PATHWAYS MKC

I need a brochure to inform and advertise the youth engagement and employment program run by Merrivale Kinship Corporation, 'BRIGHT PATHWAYS MCK'. The aim of the program is to give indigenous youth aged 14-25yrs a kickstart to life by supporting them through first time employment and achieving qualifications. I need the brochure to be easy to read and appealing to youth 14-25yrs. My target audience are indigenous youth in Australia, therefore the colours I'd like to see used are red, yellow, back, white, green and blue, these are the colours of the Aboriginal and Torres Strait flags.

I will attach:
- our logo- theres one with a white background and one with a black background.
- photos I'd like see used if possible- I want one group shot and photo at the mining site to be used.
- a word document with the information I want on the brochure
- a permission slip - I want this to be put on the end and detachable ( be able to be ripped off )

```html
<!DOCTYPE html>
<html lang="en">
<head>
<meta charset="utf-8">
<title>Bright Pathways – Youth Program Brochure</title>
<link href="https://fonts.googleapis.com/css2?family=Montserrat:wght@400;500;600;700;800&display=swap" rel="stylesheet">
<style>
:root{
  --blue:#1e8fd6;
  --blue-deep:#0f6fb8;
  --blue-light:#3fb0ec;
  --red:#e42527;
  --yellow:#f7b71d;
  --green:#8dbb3c;
  --ink:#2b2b2b;
  --grey:#5b5b5b;
  --white:#ffffff;
}
*{margin:0;padding:0;box-sizing:border-box}
html,body{width:1200px;height:849px;overflow:hidden;background:var(--white)}
body{font-family:'Montserrat',sans-serif;color:var(--ink)}
.brochure{position:relative;width:1200px;height:849px;overflow:hidden;background:var(--white)}

/* left panel */
.intro-panel{position:absolute;left:0;top:0;width:300px;height:849px;
  background:linear-gradient(160deg,var(--blue-light) 0%,var(--blue) 45%,var(--blue-deep) 100%);overflow:hidden}
.intro-panel .facet{position:absolute;inset:0}
.intro-text{position:absolute;left:27px;top:54px;width:248px;color:var(--white);
  font-size:11px;font-weight:700;line-height:1.42}
.intro-text p{margin-bottom:14px}
.eligibility{position:absolute;left:27px;top:440px;width:265px;color:var(--white)}
.eligibility h2{color:var(--yellow);font-size:12.8px;font-weight:800;line-height:1.2;text-transform:uppercase;white-space:nowrap;letter-spacing:-0.2px}
.eligibility h2 .big{font-size:19px;display:block;letter-spacing:0}
.eligibility ul{list-style:none;margin-top:16px}
.eligibility li{font-size:11.2px;font-weight:600;margin-bottom:16px;padding-left:20px;position:relative;line-height:1.35}
.eligibility li::before{content:"";position:absolute;left:0;top:2px;border-left:9px solid var(--yellow);
  border-top:5px solid transparent;border-bottom:5px solid transparent}

/* tear-off perforation for the detachable permission slip */
.perforation{position:absolute;left:298px;top:0;width:4px;height:849px;
  background:repeating-linear-gradient(180deg,var(--white) 0 6px,transparent 6px 12px);opacity:.55}

/* qualifications column */
.qualifications{position:absolute;left:316px;top:52px;width:280px}
.qualifications h2{color:var(--blue);font-size:19px;font-weight:800;line-height:1.05}
.qualifications .sub{font-size:13px;font-weight:700;color:var(--ink)}
.qual-grid{position:absolute;left:316px;top:128px;width:260px;display:grid;
  grid-template-columns:130px 130px;row-gap:16px}
.qual{text-align:center;font-size:10.5px;font-weight:700;line-height:1.25;color:var(--ink)}
.qual svg{width:46px;height:46px;display:block;margin:0 auto 6px}
.qual em{font-style:italic;font-weight:600}

.access{position:absolute;left:316px;top:488px;width:285px}
.access h2{color:var(--green);font-size:18px;font-weight:800;line-height:1.12;text-transform:uppercase}
.access ul{list-style:none;margin-top:12px}
.access li{font-size:11px;color:var(--grey);font-weight:500;padding-left:18px;position:relative;margin-bottom:7px;line-height:1.3}
.access li::before{content:"";position:absolute;left:0;top:2px;border-left:8px solid var(--yellow);
  border-top:5px solid transparent;border-bottom:5px solid transparent}

/* right column */
.accent-bar{position:absolute;left:620px;width:12px}
.accent-bar.red{top:55px;height:88px;background:var(--red)}
.accent-bar.yellow{top:405px;height:225px;background:var(--yellow)}
.what-we-do{position:absolute;left:646px;top:56px;width:300px}
.what-we-do h2{color:var(--red);font-size:20px;font-weight:800;line-height:1.1}
.what-we-do h2 span{display:block;color:var(--ink);font-weight:500}
.services{position:absolute;left:646px;top:120px;width:310px;list-style:none}
.services li{display:flex;align-items:flex-start;gap:10px;font-size:10.5px;color:var(--grey);line-height:1.35;margin-bottom:12px;font-weight:500}
.services svg{flex:0 0 26px;width:26px;height:26px}
.services b{color:var(--red);font-weight:700}

.why{position:absolute;left:646px;top:410px;width:265px}
.why h2{color:var(--yellow);font-size:18px;font-weight:800;line-height:1.1;text-transform:uppercase}
.why-body{position:absolute;left:660px;top:464px;width:258px;font-size:10.3px;color:var(--grey);line-height:1.25;font-weight:500}
.why-body p{margin-bottom:8px}
.why-body .hl{color:var(--yellow);font-style:italic;font-weight:700}

.yellow-wedge{position:absolute;left:0;top:0;width:1200px;height:660px;pointer-events:none}

/* social ribbon */
.social{position:absolute;left:930px;top:358px;width:232px;height:84px}
.social svg{position:absolute;inset:0}
.social-text{position:absolute;left:24px;top:10px;color:var(--white);font-size:11px;font-weight:600;line-height:1.42}
.social-text h3{font-size:13px;font-weight:800;margin-bottom:1px}
.social-text b{color:var(--yellow);font-weight:700}

/* bottom */
.colour-bands{position:absolute;left:300px;top:660px;width:900px;height:18px;display:flex}
.colour-bands i{flex:1}
.colour-bands .y{background:var(--yellow)}
.colour-bands .g{background:var(--green)}
.colour-bands .b{background:var(--blue)}
.photo-strip{position:absolute;left:300px;top:678px;width:900px;height:171px;
  background:linear-gradient(90deg,#6b6b6b 0%,#8c8c8c 9%,#4d6f86 11%,#3d6e91 18%,#8a8a8a 20%,#9a8a5a 31%,#b59a4f 37%,#7a7a7a 40%,#a0a0a0 50%,#5e7f45 56%,#6f9a3f 62%,#8f8f8f 66%,#b9b9b9 78%,#3f7fb0 84%,#2f78b4 90%,#9a9a9a 94%,#7d7d7d 100%)}
</style>
</head>
<body>
<div class="brochure">

  <section class="intro-panel">
    <svg class="facet" viewBox="0 0 300 849" preserveAspectRatio="none" aria-hidden="true">
      <polygon points="0,0 300,0 300,260 0,520" fill="#ffffff" opacity="0.06"/>
      <polygon points="120,849 300,500 300,849" fill="#ffffff" opacity="0.07"/>
      <polygon points="0,620 300,380 300,460 0,760" fill="#0a5ea3" opacity="0.18"/>
    </svg>
    <div class="intro-text">
      <p>Merrivale Kinship Corporation (MKC) has launched “BRIGHT PATHWAYS” which is an exciting youth engagement and employment program in Hedland and the East Pilbara.</p>
      <p>MKC wants to assist young people secure their first-time job!</p>
      <p>Washing dishes, flipping burgers, stacking shelves, lifeguarding at the pool or even starting a business! It can be anything!</p>
      <p>BRIGHT PATHWAYS will ENGAGE, EQUIP, &amp; EMPOWER young people through training and employment.</p>
      <p>Each student will undertake training and build a portfolio of achievement that makes them a “STAND OUT” candidate for prospective employers across the Pilbara.</p>
    </div>
    <div class="eligibility">
      <h2>To be eligible for the program, <span class="big">participants must be:</span></h2>
      <ul>
        <li>14–25 yrs</li>
        <li>Resident of Hedland or Newman and surrounding districts.</li>
        <li>Capable of Working flexible hours</li>
        <li>Aboriginal or Torres Strait</li>
      </ul>
    </div>
  </section>

  <div class="perforation" role="img" aria-label="Perforated tear line for the detachable permission slip"></div>

  <svg class="yellow-wedge" viewBox="0 0 1200 660" preserveAspectRatio="none" aria-hidden="true">
    <polygon points="1095,0 1200,0 1200,660 1000,660 1160,330" fill="#f7b71d"/>
  </svg>

  <section>
    <div class="qualifications">
      <h2>SOME OF THE<br>QUALIFICATIONS</h2>
      <div class="sub">WE CAN HELP YOU SECURE:</div>
    </div>
    <div class="qual-grid">
      <div class="qual">
        <svg viewBox="0 0 46 46" fill="none" stroke="#1e8fd6" stroke-width="2"><circle cx="23" cy="23" r="20"/><circle cx="23" cy="23" r="14"/><path d="M20 15h6v5h5v6h-5v5h-6v-5h-5v-6h5z"/></svg>
        Senior First Aid</div>
      <div class="qual">
        <svg viewBox="0 0 46 46" fill="none" stroke="#1e8fd6" stroke-width="2"><circle cx="23" cy="18" r="12"/><circle cx="23" cy="18" r="6"/><path d="M15 27l-5 14 6-3 3 5 4-13M31 27l5 14-6-3-3 5-4-13"/></svg>
        Bronze Medallion</div>
      <div class="qual">
        <svg viewBox="0 0 46 46" fill="none" stroke="#1e8fd6" stroke-width="2"><circle cx="23" cy="23" r="19"/><circle cx="23" cy="23" r="9"/><path d="M11 11l6 6M35 11l-6 6M11 35l6-6M35 35l-6-6"/></svg>
        Senior Lifeguard</div>
      <div class="qual">
        <svg viewBox="0 0 46 46" fill="none" stroke="#1e8fd6" stroke-width="2"><path d="M23 3l17 6v12c0 11-8 18-17 22C14 39 6 32 6 21V9z"/><path d="M16 23l5 5 9-10"/></svg>
        Young Achievers Award – <em>Bronze Award</em></div>
      <div class="qual">
        <svg viewBox="0 0 46 46" fill="none" stroke="#1e8fd6" stroke-width="2"><path d="M4 20c6-8 32-8 38 0"/><path d="M6 22h34v8H6z"/><circle cx="15" cy="30" r="6"/><circle cx="31" cy="30" r="6"/><path d="M4 40c6-4 10 4 16 0s10 4 16 0 6-2 6-2"/></svg>
        AquaTeach Swim Teacher license</div>
      <div class="qual">
        <svg viewBox="0 0 46 46" fill="none" stroke="#1e8fd6" stroke-width="2"><circle cx="23" cy="11" r="7"/><path d="M14 5h18"/><path d="M9 42c0-12 6-20 14-20s14 8 14 20z"/><path d="M19 26l4 6 4-6"/></svg>
        NSA Coaching Certificate</div>
      <div class="qual">
        <svg viewBox="0 0 46 46" fill="none" stroke="#1e8fd6" stroke-width="2"><path d="M28 2v10"/><rect x="14" y="12" width="18" height="32" rx="3"/><rect x="18" y="17" width="10" height="8"/><path d="M18 30h10M18 34h10M18 38h10"/></svg>
        Police &amp; Army Cadets</div>
    </div>

    <div class="access">
      <h2>Bright Pathways can assist students &amp; young people access:</h2>
      <ul>
        <li>TAFE Courses</li>
        <li>Traineeships and Apprenticeships</li>
        <li>Understand the labour market and apply for jobs</li>
      </ul>
    </div>
  </section>

  <section>
    <div class="accent-bar red"></div>
    <div class="what-we-do">
      <h2>WHAT WE DO THROUGH <span>BRIGHT PATHWAYS</span></h2>
    </div>
    <ul class="services">
      <li><svg viewBox="0 0 26 26" fill="none" stroke="#e42527" stroke-width="1.8"><rect x="2" y="8" width="22" height="15" rx="2"/><path d="M9 8V4h8v4M2 14h22"/></svg>
        <span><b>Apply for jobs –</b> help apply and secure your employment every step of the way.</span></li>
      <li><svg viewBox="0 0 26 26" fill="none" stroke="#e42527" stroke-width="1.8"><circle cx="10" cy="8" r="4"/><path d="M3 23c0-6 3-9 7-9s7 3 7 9"/><path d="M20 4l1.3 2.7 3 .4-2.2 2 .6 3-2.7-1.5-2.7 1.5.6-3-2.2-2 3-.4z"/></svg>
        <span><b>Support young people</b> get real &amp; relevant job qualifications e.g. Senior First Aid</span></li>
      <li><svg viewBox="0 0 26 26" fill="none" stroke="#e42527" stroke-width="1.8"><path d="M5 2h12l5 5v17H5z"/><path d="M9 10h9M9 14h9M9 18h6"/></svg>
        <span>Write up <b>outstanding resumes</b> and practise interviews.</span></li>
      <li><svg viewBox="0 0 26 26" fill="none" stroke="#e42527" stroke-width="1.8"><rect x="4" y="4" width="18" height="13" rx="1"/><path d="M1 21h24M10 10h6"/></svg>
        <span>Support <b>online training</b> – We provide the venue and laptops</span></li>
      <li><svg viewBox="0 0 26 26" fill="none" stroke="#e42527" stroke-width="1.8"><circle cx="13" cy="13" r="11"/><rect x="7" y="8" width="12" height="10" rx="1"/><circle cx="11" cy="12" r="1.6"/><path d="M14 12h3M9 15h8"/></svg>
        <span>Assist in <b>securing:</b> Photo ID, bank details, TFN, Unique Student ID (USI Number)</span></li>
      <li><svg viewBox="0 0 26 26" fill="none" stroke="#e42527" stroke-width="1.8"><circle cx="19" cy="6" r="2.5"/><path d="M4 13l7-4 5 3 4-2M1 19c3-2 5 2 8 0s5 2 8 0 5 2 8 0M1 23c3-2 5 2 8 0s5 2 8 0 5 2 8 0"/></svg>
        <span>Undertake <b>epic events</b> like the Lake Corrella 10km Marathon Swim</span></li>
    </ul>

    <div class="accent-bar yellow"></div>
    <div class="why">
      <h2>Why is Bright Pathways an important?</h2>
    </div>
    <div class="why-body">
      <p>Getting a job is not just about the money but that helps!</p>
      <p>Your first-time job is really important because it provides a future foundation for success.</p>
      <p>Young people who sign-up to BRIGHT PATHWAYS acquire the necessary confidence and work skills needed to successfully transition to adult employment.</p>
      <p>For further information, please contact Tamsin Warrick by emailing <span class="hl">youth.hedland@merrivale.org.au</span> or by calling <span class="hl">0400 318 627</span>.</p>
      <p>Other ways to contact Tamsin Warrick</p>
    </div>

    <div class="social">
      <svg viewBox="0 0 232 84" preserveAspectRatio="none" aria-hidden="true">
        <polygon points="0,6 214,0 232,42 214,84 6,78" fill="#1e8fd6"/>
        <polygon points="0,6 14,0 14,10" fill="#0f6fb8"/>
      </svg>
      <div class="social-text">
        <h3>SOCIAL MEDIA:</h3>
        <div><b>Chatline:</b> Tamsin Warrick</div>
        <div><b>Snapline:</b> twarrick1</div>
        <div><b>Picgram:</b> brightpathways_2018</div>
      </div>
    </div>
  </section>

  <div class="colour-bands"><i class="y"></i><i class="g"></i><i class="b"></i></div>
  <div class="photo-strip" role="img" aria-label="Strip of program photos: young participants in group activities, training sessions and sports in a hall, with colour tints"></div>

</div>
</body>
</html>
```